Slide Master for Holloway Engines - A Systematic Hedge Fund

We are looking for someone to produce a theme and slide master for us for our investor presentations. I have uploaded a few examples of templates that we would like to have included:
Main Title
Section Title
Slides with just bullet points
Different image/table configurations with bullet points and foot notes
Biographies of different lengths
A disclaimer (no one will read this but it should still look nice and needs to be in the presentations)
I have also uploaded the company logo, business card and colour definitions. Currently we have a blue colour scheme defined, but it would be nice to get a complementary set of colours so that when we have charts with more elements we can just draw from those.
The most important thing is that the slide master must be of general use to us. We arn't looking to have a specific presentation designed for us, but a theme/style that we can apply ourselves to any presentation we need to give in the future. It should have clearly defined guidelines for where content should go (and if this is different with and without footnotes for example). We would also like it to have a similar feel to the logo/business cards, so matt colours, high contrast, but not busy.
I'm excited to see the results!

```html
<!DOCTYPE html>
<html lang="en">
<head>
<meta charset="utf-8">
<title>Holloway Engines – Closing Slide</title>
<link rel="stylesheet" href="https://fonts.googleapis.com/css2?family=Roboto:wght@300;700&display=swap">
<style>
  :root {
    --page-bg: #e6e6e6;
    --slide-navy: #034573;
    --truss-blue: #1b5488;
    --accent-blue: #4a90d9;
    --title-white: #ffffff;
    --folio-grey: #9a9a9a;
  }
  * { margin: 0; padding: 0; box-sizing: border-box; }
  html, body {
    width: 1200px;
    height: 724px;
    overflow: hidden;
    background: var(--page-bg);
    font-family: "Roboto", Arial, sans-serif;
  }
  .sheet {
    position: relative;
    width: 1200px;
    height: 724px;
  }
  .closing-slide {
    position: absolute;
    left: 39px;
    top: 40px;
    width: 543px;
    height: 306px;
    background: var(--slide-navy);
    overflow: hidden;
  }
  .truss-decoration {
    position: absolute;
    inset: 0;
    width: 100%;
    height: 100%;
  }
  .closing-title {
    position: absolute;
    left: 58px;
    top: 108px;
    font-size: 30px;
    line-height: 1;
    font-weight: 300;
    color: var(--title-white);
    letter-spacing: -0.3px;
  }
  .closing-title strong { font-weight: 700; }
  .title-rule {
    position: absolute;
    left: 58px;
    top: 148px;
    width: 54px;
    height: 2.5px;
    background: var(--accent-blue);
  }
  .page-number {
    position: absolute;
    right: 16px;
    bottom: 9px;
    font-size: 39px;
    font-weight: 700;
    line-height: 1;
    color: var(--folio-grey);
  }
</style>
</head>
<body>
  <main class="sheet">
    <section class="closing-slide">
      <svg class="truss-decoration" viewBox="0 0 543 306" role="img" aria-label="Faint arched bridge truss motifs scattered across the slide background">
        <defs>
          <radialGradient id="trussGlow" cx="50%" cy="50%" r="50%">
            <stop offset="0%" stop-color="var(--truss-blue)" stop-opacity="0.9"/>
            <stop offset="100%" stop-color="var(--truss-blue)" stop-opacity="0"/>
          </radialGradient>
        </defs>
        <ellipse cx="109" cy="26" rx="32" ry="9" fill="url(#trussGlow)" opacity="0.6"/>
        <ellipse cx="431" cy="78" rx="70" ry="18" fill="url(#trussGlow)" opacity="0.6"/>
        <ellipse cx="145" cy="208" rx="27" ry="8" fill="url(#trussGlow)" opacity="0.6"/>
        <ellipse cx="16" cy="284" rx="20" ry="8" fill="url(#trussGlow)" opacity="0.6"/>
        <ellipse cx="410" cy="238" rx="150" ry="68" fill="url(#trussGlow)" opacity="0.8"/>
      </svg>
      <h1 class="closing-title">Thank <strong>You</strong></h1>
      <div class="title-rule"></div>
    </section>
    <div class="page-number">4</div>
  </main>
</body>
</html>
```